Business Card Design for Training Business

Clear Path Coaching is a new business that delivers training and other services with a focus on topics related to mental health and wellbeing, for example, Wellmind Response Course, Resilience etc. We have a strong focus on evidence-based psychology and neuroscience. I have a logo which I will upload with the brief, so please consider colours that work well with the logo.
Target Market(s)
Adults, workplaces (particularly government and not-for-profits)
Industry/Entity Type
Business
Contact Information for Business Card
Head Strong TrainingSamantha SellwoodDirector0438 770 850sam@headstrongtraining.com.auwww.headstrongtraining.com.au

```html
<!DOCTYPE html>
<html lang="en">
<head>
<meta charset="utf-8">
<title>Clear Path Coaching – Business Card</title>
<link rel="stylesheet" href="https://fonts.googleapis.com/css2?family=Libre+Baskerville:ital@1&family=Open+Sans:wght@300;400&display=swap">
<style>
  :root {
    --bg: #ecebe8;
    --card: #ffffff;
    --teal: #1a9c9c;
    --teal-soft: #bfe4e4;
    --ink: #222222;
    --ink-soft: #444444;
  }
  * { box-sizing: border-box; margin: 0; padding: 0; }
  html, body { width: 1200px; height: 892px; overflow: hidden; }
  body {
    background: var(--bg);
    font-family: "Open Sans", Arial, sans-serif;
    display: flex;
    align-items: center;
    justify-content: center;
    gap: 40px;
  }
  .card {
    position: relative;
    width: 540px;
    height: 309px;
    background: var(--card);
    box-shadow: 0 2px 10px rgba(0,0,0,0.12);
  }
  /* Front: contact side */
  .brand {
    position: absolute;
    left: 28px;
    top: 62px;
    width: 180px;
    text-align: center;
  }
  .brand-dot {
    width: 70px;
    height: 70px;
    margin: 0 auto 14px;
    border-radius: 50%;
    background: radial-gradient(circle, #e9f6f2 0%, var(--teal-soft) 60%, var(--teal) 100%);
  }
  .brand-name {
    font-family: "Open Sans", Arial, sans-serif;
    font-weight: 300;
    font-size: 19px;
    letter-spacing: 3px;
    line-height: 1.3;
    color: var(--ink-soft);
    text-transform: uppercase;
  }
  .divider {
    position: absolute;
    left: 232px;
    top: 40px;
    width: 3px;
    height: 230px;
    background: var(--teal);
  }
  .person {
    position: absolute;
    left: 252px;
    top: 40px;
  }
  .person-name {
    font-family: "Libre Baskerville", Georgia, serif;
    font-style: italic;
    font-size: 24px;
    color: var(--teal);
  }
  .person-role {
    font-size: 13px;
    color: var(--ink);
    margin-top: 2px;
  }
  .contacts {
    position: absolute;
    left: 252px;
    bottom: 40px;
    list-style: none;
    font-size: 14px;
    color: var(--ink);
  }
  .contacts li {
    display: flex;
    align-items: center;
    gap: 12px;
    height: 21px;
  }
  .contacts svg { width: 14px; height: 14px; flex: none; }
  /* Back: brand side */
  .card-back .brand {
    left: 0;
    right: 0;
    top: 92px;
    width: auto;
  }
  .card-back .brand-dot { width: 80px; height: 80px; }
  .card-back .brand-name { font-size: 24px; letter-spacing: 4px; }
</style>
</head>
<body>
  <section class="card card-front">
    <div class="brand">
      <div class="brand-dot"></div>
      <p class="brand-name">Clear Path<br>Coaching</p>
    </div>
    <div class="divider"></div>
    <div class="person">
      <p class="person-name">Rebecca Tanfield</p>
      <p class="person-role">Director</p>
    </div>
    <ul class="contacts">
      <li>
        <svg viewBox="0 0 14 14" aria-hidden="true"><rect width="14" height="14" fill="#111"/><path d="M4 3h2l1 2-1 1c.5 1 1 1.5 2 2l1-1 2 1v2c-4 0-7-3-7-7z" fill="#fff"/></svg>
        0491 362 517
      </li>
      <li>
        <svg viewBox="0 0 14 14" aria-hidden="true"><rect width="14" height="14" fill="#111"/><rect x="3" y="4.5" width="8" height="5.5" fill="#fff"/><path d="M3 4.5l4 3 4-3" stroke="#111" fill="none" stroke-width="0.8"/></svg>
        bec@clearpathcoaching.example.au
      </li>
      <li>
        <svg viewBox="0 0 14 14" aria-hidden="true"><rect width="14" height="14" fill="#111"/><circle cx="7" cy="7" r="4" fill="none" stroke="#fff" stroke-width="1"/><path d="M3 7h8M7 3v8" stroke="#fff" stroke-width="0.8"/></svg>
        www.clearpathcoaching.example.au
      </li>
    </ul>
  </section>

  <section class="card card-back">
    <div class="brand">
      <div class="brand-dot"></div>
      <p class="brand-name">Clear Path Coaching</p>
    </div>
  </section>
</body>
</html>
```